Calm Nest

I currently have a squarespace website www.bodysensepillow.comI want a complete design change but I want you to use the current information on the site.
Updates

We will be making a decision this week. Thank You.

```html
<!DOCTYPE html>
<html lang="en">
<head>
<meta charset="utf-8">
<title>Calm Nest — Live Well, Sleep Well</title>
<link rel="stylesheet" href="https://fonts.googleapis.com/css2?family=Montserrat:wght@500;600;700&family=Nunito:wght@400;600;700&display=swap">
<style>
  :root {
    --ink: #111111;
    --text: #333333;
    --muted: #6a6a6a;
    --paper: #ffffff;
    --hero-bg: #efeeeb;
    --black: #000000;
    --bar: rgba(48, 46, 44, 0.78);
    --label-band: rgba(60, 58, 56, 0.72);
    --social: #3a3a3a;
  }
  * { box-sizing: border-box; margin: 0; padding: 0; }
  html, body { width: 1200px; height: 3198px; overflow: hidden; background: var(--paper); }
  body { position: relative; font-family: "Nunito", sans-serif; color: var(--text); }
  .abs { position: absolute; }
  .heading { font-family: "Montserrat", sans-serif; font-weight: 700; color: var(--ink); }

  /* Header */
  .site-header { left: 0; top: 0; width: 1200px; height: 88px; }
  .brand { left: 77px; top: 22px; font-family: "Montserrat", sans-serif; font-weight: 700; font-size: 38px; letter-spacing: 1px; color: #2a2a2a; }
  .main-nav { top: 38px; left: 0; width: 1200px; font-family: "Montserrat", sans-serif; font-size: 14px; font-weight: 500; color: #444; }
  .main-nav span { position: absolute; white-space: nowrap; }
  .main-nav .current { color: var(--ink); font-weight: 600; }
  .main-nav .current::after { content: ""; position: absolute; left: 0; top: 22px; width: 20px; height: 2px; background: var(--ink); }
  .search-icon { left: 1108px; top: 38px; }

  /* Hero */
  .hero-bg { left: 0; top: 114px; width: 1200px; height: 562px; background: var(--hero-bg); }
  .hero-photo { left: 366px; top: 88px; width: 834px; height: 541px; background: linear-gradient(135deg, #efe4e2 0%, #e2d3d1 45%, #d8c6c3 70%, #ecdedd 100%); }
  .hero-title { left: 78px; top: 238px; font-size: 42px; line-height: 48px; }
  .hero-copy { left: 78px; top: 348px; width: 340px; font-size: 14px; line-height: 26px; color: var(--text); }
  .btn { display: block; width: 156px; height: 52px; border: 1px solid #222; background: var(--paper); font-family: "Montserrat", sans-serif; font-weight: 600; font-size: 16px; color: var(--ink); text-align: center; line-height: 50px; box-shadow: 10px 10px 0 var(--black); }
  .hero-btn { left: 77px; top: 446px; }
  .slider-dots { left: 78px; top: 592px; display: flex; gap: 4px; }
  .slider-dots i { width: 13px; height: 13px; border: 1px solid #555; border-radius: 50%; display: block; }
  .slider-dots i.on { background: var(--black); border-color: var(--black); }

  /* About */
  .about-block { left: 92px; top: 833px; width: 375px; height: 427px; background: var(--black); }
  .about-photo { left: 127px; top: 745px; width: 374px; height: 415px; background: linear-gradient(160deg, #f1efec 0%, #e4dfda 50%, #cfc6be 100%); }
  .about-brand { left: 92px; top: 1185px; width: 375px; text-align: center; padding-left: 70px; font-family: "Montserrat", sans-serif; font-weight: 700; font-size: 40px; color: var(--paper); }
  .about-title { left: 616px; top: 764px; font-size: 40px; }
  .about-lead { left: 616px; top: 832px; width: 340px; font-weight: 700; font-size: 16px; line-height: 24px; color: #222; }
  .about-copy { left: 618px; top: 896px; width: 380px; font-size: 14px; line-height: 27px; color: var(--muted); }
  .about-btn { left: 619px; top: 1052px; }

  .tagline { left: 0; top: 1337px; width: 1200px; text-align: center; font-size: 36px; line-height: 44px; }

  /* Feature band */
  .feature-photo { left: 0; top: 1478px; width: 1200px; height: 676px; background: linear-gradient(110deg, #a59d94 0%, #d9d2c8 30%, #ece7df 55%, #cfc6bb 80%, #e9e4dd 100%); }
  .category-bar { left: 82px; top: 1478px; width: 104px; height: 676px; background: var(--bar); }
  .category-list { left: 133px; top: 2062px; transform: rotate(-90deg); transform-origin: left top; font-family: "Montserrat", sans-serif; font-size: 19px; letter-spacing: 1px; color: #f3f3f3; white-space: nowrap; }
  .category-list b { font-weight: 400; margin: 0 14px; }
  .slide-arrow { top: 2090px; width: 42px; height: 42px; background: var(--paper); border: 1px solid #ddd; }
  .slide-arrow svg { display: block; margin: 12px auto; }

  /* Collection */
  .collection-title { left: 0; top: 2212px; width: 1200px; text-align: center; font-size: 37px; line-height: 47px; }
  .frame-top { left: 151px; top: 2349px; width: 781px; height: 13px; background: var(--black); }
  .frame-left { left: 151px; top: 2349px; width: 13px; height: 226px; background: var(--black); }
  .tile { overflow: hidden; }
  .tile-bedding { left: 164px; top: 2363px; width: 448px; height: 468px; background: linear-gradient(170deg, #c6cbc3 0%, #e5e6e2 35%, #f4f3f1 60%, #ecebe9 100%); }
  .tile-linens { left: 612px; top: 2363px; width: 437px; height: 234px; background: linear-gradient(180deg, #d6d2cb 0%, #e8e6e2 55%, #c9c5bf 100%); }
  .tile-cooling { left: 612px; top: 2597px; width: 437px; height: 234px; background: linear-gradient(160deg, #9a8f82 0%, #7ec0dc 40%, #5fb1d6 75%, #8e8a84 100%); }
  .tile-label { position: absolute; left: 0; bottom: 0; width: 100%; height: 52px; background: var(--label-band); color: var(--paper); font-size: 18px; line-height: 52px; text-align: center; }
  .bedding-label { left: 164px; top: 2736px; width: 448px; text-align: center; font-size: 20px; line-height: 31px; color: #444; }
  .viewmore-btn { left: 517px; top: 2863px; }

  /* Footer */
  .site-footer { left: 0; top: 2988px; width: 1200px; height: 210px; background: var(--black); }
  .footer-brand { left: 77px; top: 3062px; font-family: "Montserrat", sans-serif; font-weight: 700; font-size: 40px; color: var(--paper); }
  .social { top: 3032px; width: 47px; height: 47px; border-radius: 50%; background: var(--social); }
  .footer-nav { right: 78px; top: 3094px; font-size: 14px; color: #e8e8e8; white-space: nowrap; }
  .footer-nav b { font-weight: 400; margin: 0 9px; color: #aaa; }
  .copyright { right: 78px; top: 3120px; font-size: 14px; color: #e8e8e8; }
</style>
</head>
<body>

<header class="abs site-header">
  <div class="abs brand">CALM NEST</div>
  <nav class="abs main-nav">
    <span class="current" style="left:475px">HOME</span>
    <span style="left:552px">COMPANY</span>
    <span style="left:659px">PILLOWS</span>
    <span style="left:751px">SHEETS</span>
    <span style="left:835px">CONTACT US</span>
    <span style="left:960px">PRODUCTS 2019</span>
  </nav>
  <svg class="abs search-icon" width="16" height="16" viewBox="0 0 16 16" aria-label="Search">
    <circle cx="6.5" cy="6.5" r="4.8" fill="none" stroke="#222" stroke-width="2"/>
    <line x1="10" y1="10" x2="14.5" y2="14.5" stroke="#222" stroke-width="2.4" stroke-linecap="round"/>
  </svg>
</header>

<section>
  <div class="abs hero-bg"></div>
  <div class="abs hero-photo" role="img" aria-label="Woman resting on white pillows, hugging a pillow"></div>
  <h1 class="abs heading hero-title">LIVE WELL,<br>SLEEP WELL</h1>
  <p class="abs hero-copy">We custom design, private label and manufacture the highest grade sleep products in the industry at value prices.</p>
  <a class="abs btn hero-btn">CONTACT US</a>
  <div class="abs slider-dots"><i></i><i></i><i class="on"></i><i></i><i></i></div>
</section>

<section>
  <div class="abs about-block"></div>
  <div class="abs about-photo" role="img" aria-label="Woman stretching happily in bed after waking"></div>
  <div class="abs about-brand">CALM NEST</div>
  <h2 class="abs heading about-title">ABOUT US</h2>
  <p class="abs about-lead">Helping people sleep better is the most important thing that we do.</p>
  <p class="abs about-copy">Calm Nest believes that sleep is the most important part of your life.&nbsp; We created Calm Nest because better sleep makes for a better life.&nbsp; We carry a variety of speciality sleep products that are made with the finest materials available.</p>
  <a class="abs btn about-btn">LEARN MORE</a>
</section>

<h2 class="abs heading tagline">HELPING PEOPLE SLEEP BETTER IS THE MOST<br>IMPORTANT THING THAT WE DO.</h2>

<section>
  <div class="abs feature-photo" role="img" aria-label="Woman sleeping peacefully under a white duvet"></div>
  <div class="abs category-bar"></div>
  <div class="abs category-list">ALL<b>|</b>PILLOWS<b>|</b>SHEETS</div>
  <div class="abs slide-arrow" style="left:262px">
    <svg width="10" height="16" viewBox="0 0 10 16"><polyline points="8,1 2,8 8,15" fill="none" stroke="#333" stroke-width="1.5"/></svg>
  </div>
  <div class="abs slide-arrow" style="left:305px">
    <svg width="10" height="16" viewBox="0 0 10 16"><polyline points="2,1 8,8 2,15" fill="none" stroke="#333" stroke-width="1.5"/></svg>
  </div>
</section>

<section>
  <h2 class="abs heading collection-title">NEW 2019 COPPER BAMBOO BEDDING<br>COLLECTION</h2>
  <div class="abs frame-top"></div>
  <div class="abs frame-left"></div>
  <div class="abs tile tile-bedding" role="img" aria-label="Woman lying on white bamboo bedding"></div>
  <div class="abs bedding-label">2019 Copper Bamboo<br>Performance Bedding</div>
  <div class="abs tile tile-linens" role="img" aria-label="Bed made with striped pattern linens and a tray">
    <div class="tile-label">2019 Pattern Linens</div>
  </div>
  <div class="abs tile tile-cooling" role="img" aria-label="Blue textured cooling pillows on a bed">
    <div class="tile-label">2019 Cooling Performance Products</div>
  </div>
  <a class="abs btn viewmore-btn">VIEW MORE</a>
</section>

<footer class="abs site-footer"></footer>
<div class="abs footer-brand">CALM NEST</div>
<div class="abs social" style="left:966px" role="img" aria-label="Social link"></div>
<div class="abs social" style="left:1021px" role="img" aria-label="Social link"></div>
<div class="abs social" style="left:1076px" role="img" aria-label="Social link"></div>
<nav class="abs footer-nav">Home<b>|</b>Company<b>|</b>Pillows<b>|</b>Sheets<b>|</b>Contact Us<b>|</b>Products 2019</nav>
<div class="abs copyright">© CALM NEST - 2019 All Rights Reserved.</div>

</body>
</html>
```